Business card design needed

I would like a one sided black business card with the information provided above. Refer to my website www.brightvolleyracquets.com.au for an example of colors I have used for my site, would like to keep this consistent for my business cards also, I will upload my logo below.

I am a new small business that provides tennis customers with racquet re stringing, tennis strings and accessories.

Industry/Entity Type

Small Business

Contact Information for Business Card

Bright Volley Tennis

Owen Whitby
Managing Director

brightvolleyracquets@mailbox.example
www.brightvolleyracquets.com.au
0491 726 305

Racquet Restringing/Tennis Strings/Accessories

Requirements
Must have
• Must have my logo and card must be black

```html
<!DOCTYPE html>
<html lang="en">
<head>
<meta charset="utf-8">
<title>Bright Volley Tennis – Business Card</title>
<link rel="stylesheet" href="https://fonts.googleapis.com/css2?family=Open+Sans:ital,wght@0,400;0,700;1,700&display=swap">
<style>
  :root {
    --backdrop: #e7e4df;
    --card-black: #050505;
    --lime: #bcd435;
    --stripe-blue: #2f5a8f;
    --text-white: #ffffff;
    --divider: #6b6b6b;
  }
  * { margin: 0; padding: 0; box-sizing: border-box; }
  html, body {
    width: 1200px;
    height: 750px;
    overflow: hidden;
    background: var(--backdrop);
    font-family: "Open Sans", Arial, sans-serif;
  }
  .card {
    position: absolute;
    left: 75px;
    top: 75px;
    width: 1050px;
    height: 600px;
    border-radius: 44px;
    background: var(--card-black);
    overflow: hidden;
  }
  .card__band {
    position: absolute;
    left: 0;
    top: 0;
    width: 125px;
    height: 100%;
    background: var(--lime);
  }
  .card__stripe {
    position: absolute;
    left: 128px;
    top: 0;
    width: 10px;
    height: 100%;
    background: var(--stripe-blue);
  }
  .brand {
    position: absolute;
    left: 175px;
    top: 120px;
    display: flex;
    align-items: center;
    gap: 22px;
  }
  .brand__name {
    color: var(--lime);
    font-weight: 700;
    font-size: 46px;
    letter-spacing: 0.5px;
    line-height: 1;
  }
  .brand__dot {
    width: 52px;
    height: 52px;
    border-radius: 50%;
    background: var(--lime);
  }
  .contact {
    position: absolute;
    left: 172px;
    top: 370px;
    color: var(--text-white);
  }
  .contact__person {
    color: var(--lime);
    font-size: 24px;
    line-height: 1;
    margin-bottom: 18px;
  }
  .contact__name {
    font-weight: 700;
    font-size: 29px;
  }
  .contact__line {
    font-size: 24px;
    line-height: 47px;
    white-space: nowrap;
  }
  .contact__label {
    font-weight: 700;
    font-style: italic;
    margin-right: 4px;
  }
  .services {
    position: absolute;
    left: 688px;
    top: 452px;
    padding-left: 24px;
    border-left: 1px solid var(--divider);
    list-style: none;
    color: var(--text-white);
    font-size: 24px;
    line-height: 35px;
    white-space: nowrap;
  }
  .services li::before {
    content: "";
    display: inline-block;
    width: 7px;
    height: 7px;
    background: var(--text-white);
    margin-right: 8px;
    vertical-align: 5px;
  }
</style>
</head>
<body>
  <div class="card">
    <div class="card__band"></div>
    <div class="card__stripe"></div>

    <div class="brand">
      <span class="brand__name">Bright Volley Tennis</span>
      <span class="brand__dot"></span>
    </div>

    <div class="contact">
      <p class="contact__person"><span class="contact__name">Owen Whitby,</span> Managing Director</p>
      <p class="contact__line"><span class="contact__label">p :</span> 0491 726 305</p>
      <p class="contact__line"><span class="contact__label">e :</span> brightvolleyracquets@mailbox.example</p>
      <p class="contact__line"><span class="contact__label">w :</span> www.brightvolleyracquets.com.au</p>
    </div>

    <ul class="services">
      <li>Racquet Restringing</li>
      <li>Tennis Strings</li>
      <li>Accessories</li>
    </ul>
  </div>
</body>
</html>
```